Kovát Lillas Physiotherapy Business Card Vienna

We need a business card design for a newly created Physiotherapy company based in Vienna Austria.
We seek a simple, modern, minimalist design without too much color variation. The font should look young/fresh, but definitely not childish or so. Since we are a starting Business, we currently haven't got a logo, if you feel like a logo would fit your design, feel free to use one, but it's not necessary.
Target Market(s)
Healthcare, young and elderly people with mobility issues
Industry/Entity Type
Health And Wellness
Contact Information for Business Card
Name: Lilla Kovát
Title description: Physiotherapist
Phone num: +43 664 2951 4086
e-mail: lilla.praxis@bluemail.example
Colors
Designer to choose colors to be used in the design.
Requirements
Must have
- Final design language must be in German, basically, the Title Description needs to be "Physiotherapeutin" the other details remain as in the English Language.
Nice to have
- Simple, modern, minimalist design
Should not have
- too many colors, Obvious use of a skeleton, skull, spline

```html
<!DOCTYPE html>
<html lang="de">
<head>
<meta charset="utf-8">
<title>Kovát Lillas Physiotherapy – Visitenkarte</title>
<link rel="stylesheet" href="https://fonts.googleapis.com/css2?family=Montserrat:wght@300;400;700&display=swap">
<style>
  :root {
    --backdrop: #1c1c1c;
    --card: #2b2b2b;
    --card-edge: #3a3a3a;
    --ink: #ffffff;
    --ink-soft: #d6d6d6;
    --ink-muted: #a9a9a9;
  }
  html, body {
    margin: 0;
    padding: 0;
    overflow: hidden;
  }
  .canvas {
    width: 960px;
    height: 1200px;
    background: var(--backdrop);
    position: relative;
    overflow: hidden;
    font-family: "Montserrat", Arial, sans-serif;
  }
  .card {
    position: absolute;
    left: 120px;
    width: 720px;
    height: 411px;
    background: var(--card);
    border: 1px solid var(--card-edge);
    box-sizing: border-box;
    box-shadow: 0 18px 40px rgba(0,0,0,0.45);
  }
  .card--front { top: 90px; }
  .card--back  { top: 700px; }

  /* Front side */
  .contact-block {
    position: absolute;
    left: 190px;
    top: 140px;
    color: var(--ink);
  }
  .contact-block__name {
    margin: 0;
    font-weight: 700;
    font-size: 40px;
    line-height: 1.02;
    letter-spacing: 2px;
    text-transform: uppercase;
  }
  .contact-block__title {
    margin: 8px 0 14px;
    font-weight: 300;
    font-size: 18px;
    letter-spacing: 1.5px;
    color: var(--ink-soft);
    text-transform: uppercase;
  }
  .contact-block__line {
    margin: 0;
    font-weight: 400;
    font-size: 14px;
    line-height: 1.55;
    letter-spacing: 1.2px;
    color: var(--ink-soft);
    text-transform: uppercase;
  }

  /* Back side */
  .brand-block {
    position: absolute;
    left: 175px;
    top: 105px;
    color: var(--ink);
    text-transform: uppercase;
  }
  .brand-block__surname {
    margin: 0;
    font-weight: 700;
    font-size: 78px;
    line-height: 0.95;
    letter-spacing: 3px;
  }
  .brand-block__given {
    margin: 2px 0 0;
    font-weight: 700;
    font-size: 42px;
    line-height: 1;
    letter-spacing: 2px;
  }
  .brand-block__field {
    margin: 4px 0 0;
    font-weight: 300;
    font-size: 33px;
    line-height: 1.1;
    letter-spacing: 2px;
    color: var(--ink-muted);
  }
</style>
</head>
<body>
<main class="canvas">
  <section class="card card--front" aria-label="Visitenkarte Vorderseite">
    <div class="contact-block">
      <h1 class="contact-block__name">Lilla<br>Kovát</h1>
      <p class="contact-block__title">Physiotherapeutin</p>
      <p class="contact-block__line">+43 664 2951 4086</p>
      <p class="contact-block__line">lilla.praxis@bluemail.example</p>
    </div>
  </section>

  <section class="card card--back" aria-label="Visitenkarte Rückseite">
    <div class="brand-block">
      <p class="brand-block__surname">Kovát</p>
      <p class="brand-block__given">Lillas</p>
      <p class="brand-block__field">Physiotherapy</p>
    </div>
  </section>
</main>
</body>
</html>
```